Create a memorable Stationary for Security Software Company

Velbrantix is the worldwide leader in securing the Internet. Making Internet communications and critical data secure, reliable and available everywhere has been and continues to be our ongoing vision. We are committed to staying focused on real customer needs and to developing new and innovative security solutions that redefine the security landscape.

Industry/Entity Type

Internet

Font styles to use
Serif
Sans Serif
Script

Colors
0792cd
33a6d7
85cae6

```html
<!DOCTYPE html>
<html lang="en">
<head>
<meta charset="utf-8">
<title>Velbrantix Business Card</title>
<link rel="stylesheet" href="https://fonts.googleapis.com/css2?family=Open+Sans:wght@400;600&display=swap">
<style>
  :root {
    --brand-deep: #0792cd;
    --brand-mid: #33a6d7;
    --brand-light: #85cae6;
    --card-white: #ffffff;
    --backdrop: #e9ecef;
  }
  html, body {
    margin: 0;
    padding: 0;
    width: 1200px;
    height: 902px;
    overflow: hidden;
    background: var(--backdrop);
    font-family: "Open Sans", Arial, sans-serif;
  }
  .canvas {
    position: relative;
    width: 1200px;
    height: 902px;
  }
  .business-card {
    position: absolute;
    left: 130px;
    top: 183px;
    width: 940px;
    height: 536px;
    background: var(--card-white);
    border-radius: 24px;
    overflow: hidden;
    box-shadow: 0 6px 22px rgba(0, 0, 0, 0.12);
  }
  .accent-band {
    position: absolute;
    inset: 0;
    width: 940px;
    height: 536px;
  }
  .brand-mark {
    position: absolute;
    left: 70px;
    top: 180px;
    display: flex;
    align-items: center;
    gap: 16px;
  }
  .brand-dot {
    width: 64px;
    height: 64px;
    border-radius: 50%;
    background: var(--brand-mid);
  }
  .brand-name {
    font-size: 44px;
    font-weight: 600;
    color: var(--brand-deep);
    letter-spacing: 0.5px;
  }
  .identity {
    position: absolute;
    right: 38px;
    top: 76px;
    text-align: right;
  }
  .person-name {
    margin: 0;
    font-size: 31px;
    font-weight: 400;
    line-height: 1.15;
    color: var(--brand-deep);
  }
  .person-role {
    margin: 0;
    font-size: 22px;
    font-weight: 400;
    line-height: 1.2;
    color: var(--brand-light);
  }
  .contact {
    position: absolute;
    right: 38px;
    top: 320px;
    text-align: right;
    color: var(--card-white);
    font-size: 24px;
    line-height: 34px;
  }
  .address {
    margin: 0 0 10px 0;
    font-style: normal;
  }
  .contact-list {
    list-style: none;
    margin: 0;
    padding: 0;
  }
  .contact-item {
    display: flex;
    justify-content: flex-end;
    align-items: center;
    gap: 12px;
    height: 36px;
  }
  .contact-icon {
    width: 30px;
    height: 30px;
    flex: none;
  }
</style>
</head>
<body>
<main class="canvas">
  <section class="business-card">
    <svg class="accent-band" viewBox="0 0 940 536" role="img" aria-label="Blue wave decoration along the lower part of the card">
      <defs>
        <linearGradient id="bandTone" x1="0" y1="0" x2="1" y2="0">
          <stop offset="0" stop-color="#85cae6"/>
          <stop offset="0.45" stop-color="#33a6d7"/>
          <stop offset="1" stop-color="#0792cd"/>
        </linearGradient>
      </defs>
      <path fill="url(#bandTone)" d="M0,440 C300,470 540,250 940,230 L940,536 L0,536 Z"/>
    </svg>

    <div class="brand-mark">
      <span class="brand-dot"></span>
      <span class="brand-name">Velbrantix</span>
    </div>

    <header class="identity">
      <h1 class="person-name">Employee Name</h1>
      <p class="person-role">President</p>
    </header>

    <div class="contact">
      <address class="address">000 Youe Address,2nd Ste.<br>Ashbrook, Texas 1234</address>
      <ul class="contact-list">
        <li class="contact-item">
          <span>000-000-0000</span>
          <svg class="contact-icon" viewBox="0 0 30 30" aria-hidden="true">
            <rect width="30" height="30" rx="5" fill="#85cae6"/>
            <rect x="10" y="5" width="10" height="20" rx="2" fill="none" stroke="#0792cd" stroke-width="1.6"/>
            <rect x="12" y="8" width="6" height="6" fill="#0792cd"/>
          </svg>
        </li>
        <li class="contact-item">
          <span>your@yourcompany.com</span>
          <svg class="contact-icon" viewBox="0 0 30 30" aria-hidden="true">
            <rect width="30" height="30" rx="5" fill="#85cae6"/>
            <rect x="6" y="9" width="18" height="12" fill="none" stroke="#ffffff" stroke-width="1.6"/>
            <path d="M6,9 L15,16 L24,9" fill="none" stroke="#ffffff" stroke-width="1.6"/>
          </svg>
        </li>
        <li class="contact-item">
          <span>www.yourcompany.com</span>
          <svg class="contact-icon" viewBox="0 0 30 30" aria-hidden="true">
            <rect width="30" height="30" rx="5" fill="#85cae6"/>
            <circle cx="15" cy="15" r="9" fill="none" stroke="#0792cd" stroke-width="1.5"/>
            <ellipse cx="15" cy="15" rx="4" ry="9" fill="none" stroke="#0792cd" stroke-width="1.2"/>
            <line x1="6" y1="15" x2="24" y2="15" stroke="#0792cd" stroke-width="1.2"/>
          </svg>
        </li>
      </ul>
    </div>
  </section>
</main>
</body>
</html>
```